Dovetree baby skincare

design business cards (double sided) and complimentary note (single sided)

Industry/Entity Type

Business

Colors

Designer to choose colors to be used in the design.

```html
<!DOCTYPE html>
<html lang="en">
<head>
<meta charset="utf-8">
<title>Dovetree baby skincare – With Compliments slip</title>
<link rel="stylesheet" href="https://fonts.googleapis.com/css2?family=Great+Vibes&family=Playfair+Display:wght@700&display=swap">
<style>
  :root {
    --backdrop: #c8eafd;
    --paper: #ffffff;
    --peach: #f8c6a7;
    --peach-shadow: rgba(150, 95, 60, 0.28);
    --gold: #c99a32;
    --script: #f0b86c;
    --script-edge: rgba(90, 60, 30, 0.55);
    --rule: #2a2a2a;
  }
  html, body {
    margin: 0;
    padding: 0;
    width: 1200px;
    height: 950px;
    overflow: hidden;
    background: var(--backdrop);
  }
  .compliment-slip {
    position: absolute;
    left: 100px;
    top: 237px;
    width: 1000px;
    height: 476px;
    background: var(--paper);
    overflow: hidden;
  }
  .slip-waves {
    position: absolute;
    inset: 0;
    width: 100%;
    height: 100%;
  }
  .wave-band { fill: var(--peach); }
  .brand-panel {
    position: absolute;
    left: 32px;
    top: 26px;
    width: 340px;
    height: 172px;
    background: var(--paper);
    border-radius: 16px;
    box-shadow: 0 3px 8px rgba(120, 90, 70, 0.18);
    display: flex;
    align-items: center;
    justify-content: center;
  }
  .brand-name {
    font-family: "Playfair Display", Georgia, serif;
    font-weight: 700;
    font-size: 64px;
    color: var(--gold);
    letter-spacing: 0.5px;
    margin: 0;
  }
  .slip-heading {
    position: absolute;
    left: 205px;
    top: 212px;
    margin: 0;
    font-family: "Great Vibes", cursive;
    font-weight: 400;
    font-size: 96px;
    line-height: 1.1;
    color: var(--script);
    text-shadow: 1px 1px 0 var(--script-edge);
    white-space: nowrap;
  }
  .signature-rule {
    position: absolute;
    left: 110px;
    top: 384px;
    width: 470px;
    height: 0;
    border-top: 1.5px solid var(--rule);
  }
</style>
</head>
<body>
  <main class="compliment-slip">
    <svg class="slip-waves" viewBox="0 0 1000 476" preserveAspectRatio="none" aria-hidden="true">
      <defs>
        <filter id="band-shadow" x="-5%" y="-20%" width="110%" height="150%">
          <feDropShadow dx="0" dy="4" stdDeviation="5" flood-color="var(--peach-shadow)" flood-opacity="0.5"/>
        </filter>
      </defs>
      <path class="wave-band" filter="url(#band-shadow)"
        d="M0 0 H1000 V55
           C975 70, 955 78, 925 70
           C890 60, 860 52, 825 72
           C790 95, 750 110, 700 104
           C650 98, 620 60, 580 58
           C540 56, 515 90, 470 86
           C430 82, 410 50, 370 48
           L0 42 Z"/>
      <path class="wave-band" filter="url(#band-shadow)"
        d="M0 476 H1000 V372
           C970 372, 945 385, 910 392
           C870 400, 840 378, 800 380
           C755 382, 735 418, 690 420
           C645 422, 620 395, 575 400
           C530 405, 505 440, 455 442
           C405 444, 380 418, 330 422
           C280 426, 260 452, 210 452
           C160 452, 130 440, 80 440
           C45 440, 20 445, 0 446 Z"/>
    </svg>

    <div class="brand-panel">
      <p class="brand-name">Dovetree</p>
    </div>

    <h1 class="slip-heading">With Compliments</h1>

    <div class="signature-rule"></div>
  </main>
</body>
</html>
```